Harborline Lending and Capital. We provide MOSTLY residential home mortgages in Florida AND commercial loans for investment properties throughout the United states.
I would love to emulate so of the lender sites that are available on the internet but I would like to have the site as popular as possible for SEO purposes. Clients can already click the link to take them to the mortgage application where they can complete that and upload documents. If you could polish that up for me that would be great. I can also provide you with great detail on loan programs that are currently being offered. WE OFFER ALL MORTGAGE LENDING PRODUCTS. I would also like to add something in reference to the rate but I don't think it's legal to actually state or promise a rate for mortgage since they vary based on loan type, client and other criteria...

On the Harborline real estate site I would like to add a link or some way for clients to be able to put in credit card information to render services ...

Please let me know what you need from me

Thank you !!

Current link to site to improve and code

https://harborlinelendingandcapital.example/

Industry/Entity Type

Residential and commmercial lending

Coding

Coded - Design and coding required

Number of Pages Required

2 page

Requirements
Must have
• Love to integrate Mortgage interest rates even if general
Nice to have
• Link to fill out mortgage application via Quorvel LPX software

```html
<!DOCTYPE html>
<html lang="en">
<head>
<meta charset="utf-8">
<title>Harborline Lending and Capital of Florida</title>
<link href="https://fonts.googleapis.com/css2?family=Cinzel:wght@500;600;700&family=Roboto:wght@400;500;700&display=swap" rel="stylesheet">
<style>
:root{
  --forest:#1f3b1f;
  --forest-deep:#19321a;
  --lime:#8cc63f;
  --lime-soft:#a5d15c;
  --ink:#222;
  --muted:#6b6b6b;
  --paper:#fff;
  --mist:#efefef;
}
*{box-sizing:border-box;margin:0;padding:0}
html,body{width:1200px;height:4187px;overflow:hidden}
body{position:relative;font-family:"Roboto",sans-serif;color:var(--ink);background:var(--paper)}
.abs{position:absolute}
.btn{position:absolute;display:flex;align-items:center;justify-content:center;gap:8px;font:700 13px "Roboto",sans-serif;text-transform:uppercase;color:#fff;background:var(--forest);border-radius:3px;white-space:nowrap}
.btn svg{width:16px;height:16px;flex:none}
.rule{position:absolute;height:4px;width:57px;background:var(--forest);border-radius:2px}

/* header */
.brand{left:113px;top:12px;display:flex;align-items:center;gap:12px}
.brand-mark{width:64px;height:64px;border-radius:50%;background:var(--forest)}
.brand-name{color:var(--forest);font-weight:700;font-size:12px;letter-spacing:.3px;line-height:1.5}
.brand-name span{display:block;font-size:9px;letter-spacing:4.2px}
.social{width:38px;height:38px;border-radius:50%;border:1.5px solid #d6d6d6}
.social.on{background:var(--forest);border-color:var(--forest)}
.phone-dot{left:710px;top:23px;width:42px;height:42px;border-radius:50%;background:var(--lime);display:flex;align-items:center;justify-content:center}
.phone-text{left:764px;top:22px;font-size:14px;line-height:22px}
.phone-text b{font-size:16px}
.nav-band{left:393px;top:81px;width:807px;height:49px;background:var(--lime);clip-path:polygon(17px 0,100% 0,100% 100%,0 100%)}
.nav-home{left:293px;top:81px;width:117px;height:49px;background:var(--forest);clip-path:polygon(17px 0,100% 0,100% 100%,0 100%)}
.nav a{position:absolute;top:97px;color:#fff;font-weight:700;font-size:15px;text-decoration:none;text-transform:uppercase;transform:translateX(-50%);white-space:nowrap}

/* hero */
.hero{left:0;top:106px;width:1200px;height:557px;background:linear-gradient(90deg,#3f6a3a 0%,#5d8556 38%,#9aa9a0 62%,#c9cfcd 100%)}
.hero-title{position:absolute;left:114px;top:222px;font:700 48px/56px "Cinzel",serif;color:#fff;letter-spacing:1px;white-space:nowrap}
.hero-title em{font-style:normal;font-weight:500;color:var(--lime-soft)}
.dots span{position:absolute;left:44px;width:11px;height:11px;border-radius:50%;border:1.5px solid #fff}
.dots span.on{background:#fff;box-shadow:0 0 0 3px rgba(255,255,255,.4)}
.hero-btn{left:112px;top:462px;width:467px;height:50px;background:transparent;border:2px solid #fff;font-size:14px}

/* about */
.frame{position:absolute;border:2px solid #333}
.photo{position:absolute;border-radius:4px}
.sec-title{position:absolute;font:700 38px "Cinzel",serif;color:var(--forest);letter-spacing:1px;white-space:nowrap}
.about-copy{left:631px;top:862px;width:446px;font-size:14px;line-height:25.8px;color:var(--muted)}

/* products */
.products{left:0;top:1252px;width:1200px;height:860px;background:linear-gradient(180deg,#9ccc4d 0%,#88bd47 45%,#6aa23b 100%)}
.card{position:absolute;width:303px;height:262px;background:#fff;border-radius:0 0 48px 0;text-align:center;padding-top:18px}
.card .ico{width:66px;height:66px;margin:0 auto;border-radius:50%;border:1.5px solid #333;display:flex;align-items:center;justify-content:center}
.card h3{margin-top:14px;font-size:15px;line-height:23px;font-weight:700;text-transform:uppercase;color:var(--ink);padding:0 18px}
.card p{margin-top:8px;font-size:14px;line-height:22px;color:var(--muted);padding:0 14px}
.card .go{margin-top:10px}
.card.active{background:var(--forest)}
.card.active h3,.card.active p{color:#fff}
.card.active .ico{background:var(--lime);border-color:#fff}

/* properties */
.props{left:0;top:2112px;width:1200px;height:542px;background:var(--mist)}
.prop{position:absolute;top:2288px;width:233px;height:301px;background:#fff;box-shadow:0 2px 6px rgba(0,0,0,.08)}
.prop .pic{height:245px}
.prop .lbl{height:56px;display:flex;align-items:center;justify-content:center;font-weight:700;font-size:15px;text-transform:uppercase}
.prop.active .lbl{background:var(--forest);color:#fff}
.arrow{position:absolute;width:40px;height:40px;border-radius:50%;display:flex;align-items:center;justify-content:center}

/* rates */
.stats{left:104px;top:3063px;width:672px;height:199px;background:#fff;box-shadow:0 2px 12px rgba(0,0,0,.12);border-radius:3px}
.stat{position:absolute;top:3097px;width:150px;text-align:center;transform:translateX(-50%)}
.stat .ring{width:62px;height:62px;margin:0 auto;border-radius:50%;border:2px solid #ccc;border-top-color:var(--forest);display:flex;align-items:center;justify-content:center;font-weight:700;font-size:20px}
.stat p{margin-top:12px;font-size:15px;font-weight:500;line-height:25px}

/* contact */
.field{position:absolute;left:480px;width:535px;border-bottom:1.5px solid #777;font-size:13px;color:#777;padding-bottom:5px}

/* footer */
.footer{left:0;top:3649px;width:1200px;height:538px;background:var(--forest)}
.foot-name{left:406px;top:3948px;color:#fff;font-weight:700;font-size:17px;letter-spacing:1.4px;white-space:nowrap}
.foot-sub{left:395px;top:3981px;color:#fff;font-size:14px;letter-spacing:7.5px;white-space:nowrap}
.foot-nav{left:398px;top:4034px;display:flex;align-items:center;gap:14px;color:#fff;font-weight:700;font-size:15px;text-transform:uppercase;white-space:nowrap}
.foot-nav i{font-style:normal;font-weight:400;font-size:26px;color:#d8d8d8}
.fsoc{position:absolute;top:4089px;width:46px;height:46px;border-radius:50%;border:1.5px solid #fff}
.fsoc.on{background:var(--lime);border-color:var(--lime)}
.copy{left:589px;top:4103px;color:#fff;font-size:14px}
</style>
</head>
<body>

<!-- header -->
<div class="abs brand">
  <div class="brand-mark"></div>
  <div class="brand-name">HARBORLINE LENDING AND CAPITAL OF FLORIDA<span>BUSINESS AND COMMERCIAL DIVISION</span></div>
</div>
<div class="abs social on" style="left:522px;top:26px" aria-label="Social profile"></div>
<div class="abs social" style="left:576px;top:26px" aria-label="Social profile"></div>
<div class="abs social" style="left:630px;top:26px" aria-label="Social profile"></div>
<div class="abs phone-dot">
  <svg width="20" height="20" viewBox="0 0 24 24"><path fill="#1f3b1f" d="M6.6 10.8a15 15 0 0 0 6.6 6.6l2.2-2.2c.3-.3.7-.4 1-.2 1.1.4 2.3.6 3.6.6.6 0 1 .4 1 1V20c0 .6-.4 1-1 1A17 17 0 0 1 3 4c0-.6.4-1 1-1h3.5c.6 0 1 .4 1 1 0 1.3.2 2.5.6 3.6.1.3 0 .7-.2 1z"/></svg>
</div>
<div class="abs phone-text">PHONE NO:<br><b>+1 (555) 014 2290</b></div>
<div class="btn" style="left:941px;top:20px;width:145px;height:45px">Contact Us
  <svg viewBox="0 0 16 16"><circle cx="8" cy="8" r="8" fill="#fff"/><path d="M4 8h7M8 5l3 3-3 3" stroke="#1f3b1f" stroke-width="2" fill="none"/></svg>
</div>

<div class="abs hero" role="img" aria-label="Photo of a couple meeting a mortgage advisor at a desk in a bright office"></div>
<div class="dots"><span style="top:346px"></span><span class="on" style="top:364px"></span><span style="top:382px"></span></div>
<h1 class="hero-title">YOUR BEST RESOURCE<br>FOR <em>HASSLE-FREE, LOW</em><br><em>COST MORTGAGE</em><br>ORIGINATION</h1>
<div class="btn hero-btn">Fill out mortgage application to begin lending pr
  <svg viewBox="0 0 16 16"><circle cx="8" cy="8" r="8" fill="#fff"/><path d="M4 8h7M8 5l3 3-3 3" stroke="#1f3b1f" stroke-width="2" fill="none"/></svg>
</div>

<div class="abs nav-band"></div>
<div class="abs nav-home"></div>
<nav class="nav">
  <a style="left:354px">Home</a>
  <a style="left:497px">About Us</a>
  <a style="left:641px">Properties</a>
  <a style="left:813px">Loan Programs</a>
  <a style="left:1015px">Lending Products</a>
</nav>

<!-- about -->
<div class="frame" style="left:112px;top:756px;width:451px;height:390px"></div>
<div class="photo" style="left:130px;top:772px;width:449px;height:387px;background:linear-gradient(135deg,#3d5a78,#8a7260 55%,#d9a84a)" role="img" aria-label="Photo of a smiling family sitting on the floor of their new home"></div>
<h2 class="sec-title" style="left:631px;top:770px">ABOUT US</h2>
<div class="rule" style="left:631px;top:823px"></div>
<p class="abs about-copy">Harborline Lending Originates Residential Home loans in Florida and Commercial and business financing in all 50 States. We have over 25 years of experience in ALL types of real estate and commercial lending. We are strategically partnered to help you obtain ALL necessary components of residential and commercial lending. From the RIGHT lending partners to the best practice Insurance avenues and commercial and residential real estate partners</p>
<div class="btn" style="left:631px;top:1083px;width:135px;height:44px">Read More
  <svg viewBox="0 0 16 16"><circle cx="8" cy="8" r="8" fill="#fff"/><path d="M4 8h7M8 5l3 3-3 3" stroke="#1f3b1f" stroke-width="2" fill="none"/></svg>
</div>

<!-- products -->
<section class="abs products" role="img" aria-label="Soft green background of grass and leaves"></section>
<h2 class="sec-title" style="left:0;width:1200px;text-align:center;top:1308px;color:#fff">MORTGAGE LENDING PRODUCTS</h2>
<div class="rule" style="left:572px;top:1365px;background:#fff"></div>

<div class="card" style="left:114px;top:1423px">
  <div class="ico"><svg width="36" height="36" viewBox="0 0 24 24" fill="none" stroke="#222" stroke-width="1.4"><path d="M3 11l9-7 9 7M5 10v10h14V10"/><circle cx="16" cy="16" r="3"/></svg></div>
  <h3>Fixed-Rate<br>Mortgages</h3>
  <p>Lorem ipsum dolor sit amet, consecttur adipiscing elit, sed do eiusmod tempor incididunt ut labore et doloreaiqua.</p>
  <div class="go"><svg width="14" height="14" viewBox="0 0 14 14"><path d="M1 7h10M7 3l4 4-4 4" stroke="#1f3b1f" stroke-width="2.4" fill="none"/></svg></div>
</div>
<div class="card" style="left:450px;top:1423px">
  <div class="ico"><svg width="36" height="36" viewBox="0 0 24 24" fill="none" stroke="#222" stroke-width="1.4"><path d="M3 11l9-7 9 7M5 10v10h14V10"/><path d="M9 17l6-6M9.5 11.5h.01M14.5 16.5h.01"/></svg></div>
  <h3>Adjustable-Rate Mortgages<br>(ARMs)</h3>
  <p>Lorem ipsum dolor sit amet, consecttur adipiscing elit, sed do eiusmod tempor incididunt ut labore et doloreaiqua.</p>
  <div class="go"><svg width="14" height="14" viewBox="0 0 14 14"><path d="M1 7h10M7 3l4 4-4 4" stroke="#1f3b1f" stroke-width="2.4" fill="none"/></svg></div>
</div>
<div class="card" style="left:785px;top:1423px">
  <div class="ico"><svg width="36" height="36" viewBox="0 0 24 24" fill="none" stroke="#222" stroke-width="1.4"><path d="M4 20V12M9 20V9M14 20V13M19 20V6M3 20h18"/></svg></div>
  <h3>Interest-Only<br>Mortgages</h3>
  <p>Lorem ipsum dolor sit amet, consecttur adipiscing elit, sed do eiusmod tempor incididunt ut labore et doloreaiqua.</p>
  <div class="go"><svg width="14" height="14" viewBox="0 0 14 14"><path d="M1 7h10M7 3l4 4-4 4" stroke="#1f3b1f" stroke-width="2.4" fill="none"/></svg></div>
</div>
<div class="card" style="left:114px;top:1724px">
  <div class="ico"><svg width="36" height="36" viewBox="0 0 24 24" fill="none" stroke="#222" stroke-width="1.4"><path d="M3 11l9-7 9 7M5 10v10h14V10M10 20v-5h4v5"/></svg></div>
  <h3>FHA Loans (Federal Housing Administration)</h3>
  <p>Lorem ipsum dolor sit amet, consecttur adipiscing elit, sed do eiusmod tempor incididunt ut labore et doloreaiqua.</p>
  <div class="go"><svg width="14" height="14" viewBox="0 0 14 14"><path d="M1 7h10M7 3l4 4-4 4" stroke="#1f3b1f" stroke-width="2.4" fill="none"/></svg></div>
</div>
<div class="card active" style="left:450px;top:1724px">
  <div class="ico"><svg width="36" height="36" viewBox="0 0 24 24" fill="none" stroke="#1f3b1f" stroke-width="1.6"><path d="M12 3l2.6 5.3 5.9.9-4.3 4.1 1 5.8L12 16.4 6.8 19.1l1-5.8L3.5 9.2l5.9-.9z"/></svg></div>
  <h3>VA Loans (Veterans<br>Affairs)</h3>
  <p>Lorem ipsum dolor sit amet, consecttur adipiscing elit, sed do eiusmod tempor incididunt ut labore et doloreaiqua.</p>
</div>
<div class="card" style="left:785px;top:1724px">
  <div class="ico"><svg width="36" height="36" viewBox="0 0 24 24" fill="none" stroke="#222" stroke-width="1.4"><path d="M3 11l9-7 9 7M5 10v10h14V10"/><circle cx="12" cy="15" r="3"/></svg></div>
  <h3>Conventional<br>Loans</h3>
  <p>Lorem ipsum dolor sit amet, consecttur adipiscing elit, sed do eiusmod tempor incididunt ut labore et doloreaiqua.</p>
  <div class="go"><svg width="14" height="14" viewBox="0 0 14 14"><path d="M1 7h10M7 3l4 4-4 4" stroke="#1f3b1f" stroke-width="2.4" fill="none"/></svg></div>
</div>
<div class="btn" style="left:532px;top:2015px;width:135px;height:45px;background:#fff;color:var(--forest)">Read More
  <svg viewBox="0 0 16 16"><circle cx="8" cy="8" r="8" fill="#1f3b1f"/><path d="M4 8h7M8 5l3 3-3 3" stroke="#fff" stroke-width="2" fill="none"/></svg>
</div>

<!-- properties -->
<section class="abs props"></section>
<h2 class="sec-title" style="left:0;width:1200px;text-align:center;top:2177px">AVAILABLE PROPERTIES</h2>
<div class="rule" style="left:570px;top:2233px;width:60px"></div>
<div class="prop" style="left:112px"><div class="pic" style="background:linear-gradient(160deg,#cfd6dc,#8c9296)" role="img" aria-label="Photo of a modern white house with balconies"></div><div class="lbl">12 Sunset Street</div></div>
<div class="prop active" style="left:359px"><div class="pic" style="background:linear-gradient(160deg,#3c4a55,#1e242a)" role="img" aria-label="Photo of a dark modern house at dusk"></div><div class="lbl">34 Union Avenue</div></div>
<div class="prop" style="left:608px"><div class="pic" style="background:linear-gradient(180deg,#a9c3da,#d8d8d2 60%,#b89b74)" role="img" aria-label="Photo of a contemporary home with a perforated facade"></div><div class="lbl">56 Washington Street</div></div>
<div class="prop" style="left:855px"><div class="pic" style="background:linear-gradient(90deg,#8a4a3e,#3c4c5a 55%,#6e8fb0)" role="img" aria-label="Photo of a brick and glass building facade"></div><div class="lbl">78 Oak Boulevard</div></div>
<div class="arrow" style="left:39px;top:2419px;background:var(--forest);box-shadow:0 0 0 4px #d2d2d2"><svg width="14" height="14" viewBox="0 0 14 14"><path d="M9 2L4 7l5 5" stroke="#fff" stroke-width="2" fill="none"/></svg></div>
<div class="arrow" style="left:1124px;top:2421px;border:1.5px solid #222"><svg width="14" height="14" viewBox="0 0 14 14"><path d="M5 2l5 5-5 5" stroke="#222" stroke-width="2" fill="none"/></svg></div>

<!-- rates -->
<h2 class="sec-title" style="left:112px;top:2730px;font-size:44px;line-height:49px">OUR MORTGAGE<br>INTEREST RATES</h2>
<div class="rule" style="left:112px;top:2835px;width:60px"></div>
<p class="abs" style="left:110px;top:2868px;width:470px;font-size:14px;line-height:26px;color:var(--muted)">Lorem ipsum dolor sit amet, consectetur adipiscing elit, sed do eius-mod tempor incididunt ut labore et dolore magna aliqua. Ut enim ad minim veniam, quis nostrud exercitation ullamco laboris nisi ut liquip ex ea commodo consequat. Duis aute irure dolor in.</p>
<div class="btn" style="left:112px;top:2985px;width:145px;height:46px">Learn More
  <svg viewBox="0 0 16 16"><circle cx="8" cy="8" r="8" fill="#fff"/><path d="M4 8h7M8 5l3 3-3 3" stroke="#1f3b1f" stroke-width="2" fill="none"/></svg>
</div>
<div class="frame" style="left:629px;top:2750px;width:451px;height:442px"></div>
<div class="photo" style="left:613px;top:2766px;width:449px;height:437px;background:linear-gradient(135deg,#e3e6e8,#b8bfc4 50%,#7a6e62)" role="img" aria-label="Photo of hands holding a small model house above stacked coins"></div>
<div class="abs stats"></div>
<div class="stat" style="left:195px"><div class="ring">52%</div><p>Fixed<br>Rate Mortgages</p></div>
<div class="stat" style="left:363px"><div class="ring">82%</div><p>Adjustable-Rate<br>Mortgages</p></div>
<div class="stat" style="left:532px"><div class="ring">57%</div><p>Interest-Only<br>Mortgages</p></div>
<div class="stat" style="left:701px"><div class="ring">76%</div><p>Hybrid<br>ARMs</p></div>

<!-- contact & footer -->
<section class="abs footer"></section>
<div class="photo" style="left:0;top:3354px;width:595px;height:441px;border-radius:0;background:linear-gradient(120deg,#e6dccb,#b98f5e 55%,#5b4a36)" role="img" aria-label="Photo of a couple reviewing documents with an advisor"></div>
<div class="frame" style="left:707px;top:3374px;width:382px;height:231px"></div>
<div class="abs" style="left:424px;top:3382px;width:659px;height:460px;background:#fff"></div>
<h2 class="sec-title" style="left:480px;top:3424px;font-size:44px">GET IN TOUCH</h2>
<div class="rule" style="left:480px;top:3480px;width:60px"></div>
<div class="field" style="top:3521px">Name</div>
<div class="field" style="top:3585px">Email</div>
<div class="field" style="top:3648px">Phone Number</div>
<div class="field" style="top:3712px">Message</div>
<div class="btn" style="left:483px;top:3760px;width:146px;height:45px">Submit Now
  <svg viewBox="0 0 16 16"><circle cx="8" cy="8" r="8" fill="#fff"/><path d="M4 8h7M8 5l3 3-3 3" stroke="#1f3b1f" stroke-width="2" fill="none"/></svg>
</div>

<div class="abs" style="left:160px;top:3910px;width:200px;height:200px;border-radius:50%;background:#fff"></div>
<div class="abs foot-name">HARBORLINE LENDING AND CAPITAL OF FLORIDA</div>
<div class="abs foot-sub">BUSINESS AND COMMERCIAL DIVISION</div>
<nav class="abs foot-nav"><span>Home</span><i>/</i><span>About Us</span><i>/</i><span>Properties</span><i>/</i><span>Loan Programs</span><i>/</i><span>Lending Products</span></nav>
<div class="fsoc on" style="left:390px" aria-label="Social profile"></div>
<div class="fsoc" style="left:457px" aria-label="Social profile"></div>
<div class="fsoc" style="left:522px" aria-label="Social profile"></div>
<div class="abs copy">© 2025. All Rights Reserved.</div>

</body>
</html>
```